Stage Design Company Business Card

We are looking to step up up our business card design for our team.

We are a Full service Design and Consultation company for Stage and TV with an emphasis in Theatrical Lighting.

We like our materials to be clean and modern with solid colors free of patterns and gradients. Our brand consists of 4 primary colors Purple, Black, Grey, and White. Provided is our Word Mark as well as our Symbol Logo.

We would like our cards to leave an impression beyond the information, show our attention to design and detail, and make our marks an easily recognized feature (together or apart) for our clients.

We need a warm approachable comfortable feel for some clients, and a professional flair for the board member type clients.

Attached are our brand elements, and our existing cards to give a sense of our style and a glipse at the information we provide on our cards.

Target Market(s)

broad client base from church leaders to high school teachers and architects.

Industry/Entity Type

Business

Contact Information for Business Card

We format our phone number with periods not parenthesis or dashes. Information will be edited for each of our team members, and team member specific cards are not part of this scope, but rather a template so to speak.

Font styles to use
Sans Serif

Colors
6b449b
ffffff
000000
333333
aaaaaa

Requirements
Must have
• Wordmark and logo mark present (does not need to exist on the same side of card)
• Brand Colors,
• Name, Phone, Email, Address.
• Unique choices that make someone stop and take a second look
Nice to have
• It would be nice to somehow convey what we DO, as our brand name does not lend itself to this, outside of an obvious tagline though.....
• social media if not crowded. all of our handles match (instagram, twitter, facebook)
Should not have
• "clipart"

```html
<!DOCTYPE html>
<html lang="en">
<head>
<meta charset="utf-8">
<title>Zavri Business Card</title>
<link rel="stylesheet" href="https://fonts.googleapis.com/css2?family=Open+Sans:wght@400;600;700&display=swap">
<style>
  :root {
    --stage-black: #000000;
    --card-paper: #f2f2f2;
    --brand-purple: #3b2470;
    --ink-purple: #2e1f66;
    --ink-dark: #333333;
    --ink-light: #ffffff;
  }
  * { margin: 0; padding: 0; box-sizing: border-box; }
  html, body {
    width: 1200px; height: 899px; overflow: hidden;
    background: var(--stage-black);
    font-family: "Open Sans", sans-serif;
  }
  .canvas { position: relative; width: 1200px; height: 899px; }

  .card { position: absolute; top: 200px; width: 310px; height: 500px; }
  .card-front {
    left: 264px; background: var(--card-paper);
    border-radius: 50px 0 56px 0;
  }
  .card-back {
    left: 641px; background: var(--brand-purple);
    border-radius: 0 50px 0 56px;
  }

  .brand-lockup {
    position: absolute; left: 26px; top: 88px;
    display: flex; align-items: center; gap: 33px;
  }
  .brand-dot {
    width: 56px; height: 56px; border-radius: 50%;
    background: var(--ink-purple);
  }
  .wordmark {
    font-weight: 600; font-size: 27px; letter-spacing: 18px;
    color: var(--ink-purple);
  }

  .contact { position: absolute; left: 33px; top: 300px; color: var(--ink-dark); }
  .person-name { font-size: 19px; font-weight: 600; color: var(--ink-purple); line-height: 1.2; }
  .person-role { font-size: 14px; line-height: 1.3; }
  .address { font-size: 14px; line-height: 1.3; margin-top: 22px; }
  .channels { list-style: none; margin-top: 12px; font-size: 14px; line-height: 1.3; }
  .channels li { display: flex; align-items: center; gap: 8px; }
  .channels svg { width: 11px; height: 11px; fill: var(--ink-purple); flex: none; }

  .back-field { position: absolute; inset: 0; border-radius: inherit; background: var(--brand-purple); }
  .back-wordmark {
    position: absolute; left: 0; right: 0; top: 415px; text-align: center;
    font-weight: 600; font-size: 36px; letter-spacing: 22px; padding-left: 22px;
    color: var(--ink-light);
  }
</style>
</head>
<body>
<main class="canvas">
  <section class="card card-front">
    <div class="brand-lockup">
      <span class="brand-dot"></span>
      <span class="wordmark">ZAVRI</span>
    </div>
    <div class="contact">
      <p class="person-name">Marcus Hale</p>
      <p class="person-role">Managing Director</p>
      <p class="address">12345, Address Goes Here<br>Country Name, 123456.</p>
      <ul class="channels">
        <li><svg viewBox="0 0 24 24"><path d="M6.6 10.8a15 15 0 0 0 6.6 6.6l2.2-2.2c.3-.3.7-.4 1-.2 1.1.4 2.3.6 3.6.6.6 0 1 .4 1 1V20c0 .6-.4 1-1 1A17 17 0 0 1 3 4c0-.6.4-1 1-1h3.5c.6 0 1 .4 1 1 0 1.3.2 2.5.6 3.6.1.3 0 .7-.2 1z"/></svg>044-555 010 246</li>
        <li><svg viewBox="0 0 24 24"><path d="M2 5h20v14H2z M2 5l10 7 10-7" /></svg>hello@zavristage.com</li>
        <li><svg viewBox="0 0 24 24"><path d="M10 14a4 4 0 0 1 0-5.7l3-3a4 4 0 0 1 5.7 5.7l-1.5 1.5-1.4-1.4 1.5-1.5a2 2 0 0 0-2.9-2.9l-3 3a2 2 0 0 0 0 2.9zm4-4a4 4 0 0 1 0 5.7l-3 3a4 4 0 0 1-5.7-5.7l1.5-1.5 1.4 1.4-1.5 1.5a2 2 0 0 0 2.9 2.9l3-3a2 2 0 0 0 0-2.9z"/></svg>www.zavristage.com</li>
      </ul>
    </div>
  </section>

  <section class="card card-back">
    <div class="back-field" role="img" aria-label="Large faint brand symbol decoration on purple"></div>
    <p class="back-wordmark">ZAVRI</p>
  </section>
</main>
</body>
</html>
```